IT Company needs Website for new Web and Mobile products for Sports and Fitness

Background:

We developed web based white label frontend web solution, backend services and white label mobile apps for to log, analyze, share and control sport and fitness activities. The name of this product suite is "Trevantix" (http://trevantix-example.com)

This products will be used by customers that provide platforms and community systems for sport and fitness. One of the major USP's is, that our technology i open for nearly all common formats, devices and apps out in the market. This means, you can just upload your data directly from device, file or app - e.G. Kestrel, Bolvane, Ravelo, StrideVault, Pacelumo, Zembra and much others.

Two current concrete examples/References

(1) MyQuorel
It's an international platform from quorel for runners. It provides individual training lans and a training log. MyQuorel uses the Backend Product "Trevantix Hub" (see http://hub.trevantix-example.net for a landing page) to integrate device, file and app support. Before this, every user has to track his training with manual inputs

(2) Paceharbor and fen-zine
Both are German customers. Paceharor is focused on runners. fen-zine is focused on Triatheletes. Both use the Product "Trevantix Web". This is a complete web solution with web based frontend solutions for athletes and coaches.

What do we need?
We need website layout for B2B for our products. We don't need lot's of pages. We need the pretty and nice layout, so we can derive the pages we need.

IMPORTANT
We don't talk about the webpages for the product itself (this will be a different project in future). We talk about a website, explaining the products)
Updates

Hi all,

we just start reviewing the first designs, and try to give feedback as detailed as possible. We attached a PDF document, to describe the the products a little bit more detailed. 

As written in the description, in the end we have two different sections. One is the usual stuff like "start page", "about", "contact", "disclaimer", "pricing", "blah...." and one will be the Developer Section, the "Tec Section". This ist aimed to developers (of our customers) that will integrate our products in there existing system or which will integrate our services in there own software.  This "pages" are more like "documentation", so easy to read and cool to look at (cause developers likes it cool, but straight)

Dear all,

we just do the final review. Cause this week is with heavy load, it takes some time...

Cheers

Odell

Target Market(s)

* Platforms and Communities for sport, health and fitness
* Gyms

Industry/Entity Type

Concrete

Font styles to use
Sans Serif

Requirements
Must have
• * Templates shall base on bootstrap. If not, it shall be easily realized on our site with bootstrap or out of the box "full responsive"

* HTML5 / CSS3
Nice to have
• PAGES
- Start Page
- Generic Template (from which we can derive additional pages)
- Contact Page
- Disclaimer Page
- Blog/News Page
- "About us" Page (can be combined with disclaimer)
- One Example product page (in end we have 3 products), shall show (if you need product details, let me know)
- product and it's description
- pricing information
- Add-Ons for the product
- Developer Section Page (Start Point for developers, where the finde "basic technical concepts and developer API's
- Example Developer Page for technical concept
- Example Developer Page for API

LOGO ISSUE
You can use an align to the Logo attached OR provide a new logo. The given logo is a logo for our own B2C Website http://trevantix-example.net. It's not really necessary, that the logo or the color must be used for the product website. Maybe it will be better if it's a complete new one, to avoid irritation between Trevantix as a B2B product and trevantix-example.net as a B2C platform.
Should not have
• No Flash and other proprietary technologies

```html
<!DOCTYPE html>
<html lang="en">
<head>
<meta charset="utf-8">
<title>Trevantix – Pricing</title>
<link rel="stylesheet" href="https://fonts.googleapis.com/css2?family=PT+Sans+Narrow:wght@400;700&family=Source+Sans+3:wght@400;600&display=swap">
<style>
:root{
  --orange:#e8790f;
  --orange-light:#f2a526;
  --ink:#3a3a3a;
  --text:#4a4a4a;
  --navy:#1f3148;
  --red:#e01818;
  --line:#d8d8d8;
  --footer:#262626;
  --white:#ffffff;
}
*{margin:0;padding:0;box-sizing:border-box}
html,body{width:1200px;height:1196px;overflow:hidden;background:var(--white)}
body{position:relative;font-family:"Source Sans 3",sans-serif;color:var(--text)}
.abs{position:absolute}

/* header */
.brand{left:182px;top:18px;font-family:"Source Sans 3",sans-serif;font-weight:600;font-size:34px;color:var(--orange);display:flex;align-items:center;gap:8px;line-height:1}
.brand-mark{width:14px;height:14px;background:var(--orange);border-radius:50%}
.brand-tag{left:182px;top:64px;font-size:8.5px;font-weight:600;letter-spacing:.2px;color:#222;text-transform:uppercase}
.nav{top:39px;left:0;width:1200px;height:20px}
.nav a{position:absolute;top:1px;font-size:11px;color:#555;text-decoration:none;text-transform:uppercase;transform:translateX(-50%)}
.nav .sep{position:absolute;top:-5px;width:1px;height:24px;background:var(--line)}

/* hero */
.hero{left:0;top:99px;width:1200px;height:262px;background:linear-gradient(100deg,#f6e2b8 0%,#f3c877 25%,#e7a24f 50%,#c7673a 72%,#9c4a30 100%)}
.hero-title{left:182px;top:139px;font-family:"PT Sans Narrow",sans-serif;font-weight:700;font-size:33px;line-height:40px}
.hero-title .l1{color:var(--orange);display:block}
.hero-title .l2{color:#3d3a36;display:block}
.signup{left:180px;top:247px;width:383px;height:39px;background:var(--white);border:1px solid #d6d6d6;border-radius:3px;display:flex;align-items:center}
.signup span{padding-left:16px;font-size:10.5px;color:#8a8a8a;text-transform:uppercase;flex:1}
.signup button{width:133px;height:35px;margin-right:2px;border:1px solid #c07a08;border-radius:3px;background:linear-gradient(#f6b52a,#dc8a07);color:var(--white);font-family:"Source Sans 3",sans-serif;font-size:16px;text-transform:uppercase}

/* pricing */
.page-title{left:213px;top:378px;font-family:"PT Sans Narrow",sans-serif;font-weight:700;font-size:23px;color:var(--navy)}
.title-rule{left:214px;top:427px;width:412px;height:6px;background:radial-gradient(ellipse at center,rgba(0,0,0,.08),rgba(0,0,0,0) 70%)}
.card{left:206px;top:463px;width:808px;height:623px;border:1px solid #d4d4d4;border-radius:5px;box-shadow:inset 0 0 12px rgba(0,0,0,.08)}
.section-title{left:244px;top:498px;font-size:20px;color:var(--ink);display:flex;align-items:center;gap:8px}
.section-title i{width:10px;height:10px;border-radius:50%;background:var(--orange);display:inline-block}
.product-name{left:279px;font-size:17px;color:var(--ink)}
.product-photo{left:279px;width:195px;height:108px;border:2px solid #cfcfcf;border-radius:4px}
.product-desc{left:490px;width:472px;font-size:11.3px;line-height:15.5px;color:#555}
.price{left:490px;font-size:13px;color:#555;display:flex;align-items:baseline;gap:10px}
.price s{color:var(--red);font-size:17px}
.price b{color:var(--red);font-size:20px;font-weight:400;margin-left:2px}
.more{left:494px;font-size:11.5px;color:var(--red);text-decoration:none}

/* footer */
.footer-rule{left:0;top:1124px;width:1200px;border-top:1px dotted #999}
.footer{left:0;top:1127px;width:1200px;height:69px;background:var(--footer)}
.social{left:210px;top:1147px;display:flex;gap:11px}
.social span{width:22px;height:22px;border-radius:2px;display:block}
.copy{right:229px;top:1142px;font-size:11.5px;color:#cfcfcf}
</style>
</head>
<body>

<header>
  <div class="abs brand"><span class="brand-mark"></span>Trevantix</div>
  <div class="abs brand-tag">Digital sport and fitness services</div>
  <nav class="abs nav">
    <a style="left:448px">Home</a><span class="sep" style="left:491px"></span>
    <a style="left:543px">Trevantix</a><span class="sep" style="left:593px"></span>
    <a style="left:659px">Fitness Cloud</a><span class="sep" style="left:723px"></span>
    <a style="left:781px">References</a><span class="sep" style="left:838px"></span>
    <a style="left:893px">Products</a><span class="sep" style="left:948px"></span>
    <a style="left:998px">Services</a>
  </nav>
</header>

<section>
  <div class="abs hero" role="img" aria-label="Photo of a runner's red running shoes on a track at sunset"></div>
  <h1 class="abs hero-title"><span class="l1">DIE OFFENE SPORT- UND</span><span class="l2">FITNESSPLATFORM FUR JEDEN SPORT</span></h1>
  <form class="abs signup"><span>What's your email address :</span><button type="button">Join for free</button></form>
</section>

<main>
  <h2 class="abs page-title">Pricing</h2>
  <div class="abs title-rule"></div>
  <div class="abs card"></div>
  <h3 class="abs section-title"><i></i>Retrieve Data From Devices</h3>

  <h4 class="abs product-name" style="top:543px">Sport Watches</h4>
  <div class="abs product-photo" style="top:576px;background:linear-gradient(120deg,#555,#2a2a2a 50%,#7a3a62)" role="img" aria-label="Photo of two GPS sport watches"></div>
  <p class="abs product-desc" style="top:576px">Sed ut perspiciatis unde omnis iste natus error sit voluptatem accusantium doloremque laudantium, totam rem aperiam, eaque ipsa quae ab illo inventore veritatis et quasi architecto beatae vitae dicta sunt explicabo.</p>
  <div class="abs price" style="top:628px">Price :<s>$240</s><b>$195</b></div>
  <a class="abs more" style="top:660px">More&gt;&gt;</a>

  <h4 class="abs product-name" style="top:715px">Cardio Devices</h4>
  <div class="abs product-photo" style="top:748px;background:linear-gradient(90deg,#3a3a3a 0 25%,#eee 25% 75%,#3a3a3a 75%)" role="img" aria-label="Photo of heart rate monitor devices"></div>
  <p class="abs product-desc" style="top:748px">Sed ut perspiciatis unde omnis iste natus error sit voluptatem accusantium doloremque laudantium, totam rem aperiam, eaque ipsa quae ab illo inventore veritatis et quasi architecto beatae vitae dicta sunt explicabo.</p>
  <div class="abs price" style="top:800px">Price :<s>$240</s><b>$195</b></div>
  <a class="abs more" style="top:832px">More&gt;&gt;</a>

  <h4 class="abs product-name" style="top:904px">Sport- and Fitness Tracker</h4>
  <div class="abs product-photo" style="top:938px;background:linear-gradient(110deg,#2a2a2a,#777 50%,#bbb)" role="img" aria-label="Black and white photo of an athlete wearing a fitness tracker"></div>
  <p class="abs product-desc" style="top:938px">Sed ut perspiciatis unde omnis iste natus error sit voluptatem accusantium doloremque laudantium, totam rem aperiam, eaque ipsa quae ab illo inventore veritatis et quasi architecto beatae vitae dicta sunt explicabo.</p>
  <div class="abs price" style="top:990px">Price :<s>$240</s><b>$195</b></div>
  <a class="abs more" style="top:1022px">More&gt;&gt;</a>
</main>

<footer>
  <div class="abs footer-rule"></div>
  <div class="abs footer"></div>
  <div class="abs social" aria-label="Social links">
    <span style="background:#3b5a99"></span>
    <span style="background:#3fb2e3"></span>
    <span style="background:#ededed"></span>
    <span style="background:#f09a1e"></span>
    <span style="background:#d32020"></span>
    <span style="background:#6f8ea8"></span>
  </div>
  <div class="abs copy">© 2013 trevantix-example.com, All rights reserved</div>
</footer>

</body>
</html>
```